Web site for radio show

I've got a radio show starting on OrbitalWave and need a web site for it. I am familiar with WordPress, so I'd like to get a design for a WordPress-based web site for the show.

I'm also posting a logo project to be done at the same time.

The best radio show web site I've seen is the Cosmic Tuesday site (www.cosmictuesday-example.com). That's a good model but I don't want to start with that much complexity and content. The initial site that I'd like you to design would have the following parts:
- Upcoming shows
- Past shows (including links to authors, their web sites, and their books)
- Twitter feed
- Blog
- About
- ...and anything else you think would be necessary

For colors, I'd like it to be consistent with my personal web site: www.kellaway-ventures-example.com

Target Market(s)

The target market for this show is mid- to upper-level managers

Industry/Entity Type

Radio

Requirements
Must have
• The project has to proceed in (at least) two stages: a first rough layout, and a second finished design. Whether you want a third stage in between with look and feel options is up to you.

```html
<!DOCTYPE html>
<html lang="en">
<head>
<meta charset="utf-8">
<title>Kellaway Show</title>
<link href="https://fonts.googleapis.com/css2?family=Alfa+Slab+One&family=PT+Sans:wght@400;700&display=swap" rel="stylesheet">
<style>
:root{
  --red:#9b0a0a;
  --red-soft:#b33a3a;
  --text:#3a3a3a;
  --muted:#777;
  --footer:#3b3b3d;
  --white:#fff;
  --sepia-1:#e8dcc4;
  --sepia-2:#8a7a62;
}
*{margin:0;padding:0;box-sizing:border-box}
html,body{width:1042px;height:1200px;overflow:hidden;background:var(--white)}
body{position:relative;font-family:"PT Sans",sans-serif;color:var(--text);font-size:8.5px;line-height:1.45}
.abs{position:absolute}
.topbar{left:0;top:0;width:1042px;height:69px;background:var(--red);border-bottom:2px solid #d9a3a3}
.brand{left:180px;top:14px;font-family:"Alfa Slab One",serif;color:var(--white);font-size:30px;letter-spacing:.5px}
.phone{left:766px;top:21px;color:var(--white);font-weight:700;font-size:12px;display:flex;align-items:center;gap:6px}
.follow{left:723px;top:42px;color:var(--white);font-size:10px;display:flex;align-items:center;gap:3px}
.follow .sq{width:17px;height:17px;background:var(--white);margin-left:2px}
.nav{left:0;top:71px;width:1042px;height:34px;background:linear-gradient(#fff,#ececec);border-bottom:1px solid #ddd}
.nav ul{list-style:none;display:flex;position:absolute;left:183px;top:8px;font-size:14px;color:var(--red)}
.nav li+li::before{content:"|";margin:0 11px}
.hero{left:0;top:106px;width:1042px;height:345px;background:radial-gradient(ellipse at 55% 35%,#fbf6ea 0%,var(--sepia-1) 35%,var(--sepia-2) 80%,#4c4236 100%)}
.hero-mic{left:610px;top:110px;width:220px;height:340px;background:linear-gradient(160deg,#d8d2c6,#3a3834);border-radius:110px 110px 20px 20px;opacity:.75}
.hero-title{left:200px;top:150px;font-family:"Alfa Slab One",serif;font-size:40px;color:#111}
.hero-copy{left:206px;top:212px;width:345px;font-size:9px;color:#222;line-height:1.25}
.arrow{top:250px;width:38px;height:51px;background:var(--red);display:flex;align-items:center;justify-content:center}
.dots{left:790px;top:421px;display:flex;gap:5px}
.dots span{width:10px;height:10px;border-radius:50%;background:var(--white);border:1px solid #999}
.dots .on{background:var(--red);box-shadow:inset 0 0 0 2px #fff}
h2{position:absolute;font-weight:400;color:var(--red);font-size:15px;text-transform:uppercase}
.body-copy{font-size:8.5px;text-align:justify}
.more{font-size:8.5px;color:var(--red)}
.photo{background:linear-gradient(160deg,#9a7dd6,#4b2a7a 55%,#120c22)}
.showcard{left:206px;top:868px;width:267px;height:72px;background:var(--red-soft);color:var(--white);padding:6px 8px}
.showcard .name{font-size:13px}
.showcard .desc{font-size:7.5px;width:160px;line-height:1.4}
.showcard .share{font-size:11px;display:flex;align-items:center;gap:4px;margin-top:2px}
.showcard .share i{width:17px;height:17px;border-radius:50%;background:var(--white);display:inline-block;opacity:.9}
.showcard .date{position:absolute;right:7px;top:6px;font-size:26px;text-align:center;line-height:1.1}
.socialbar{left:525px;top:918px;display:flex;gap:10px;align-items:center;font-size:7.5px;color:#555}
.socialbar .btn{border:1px solid #ccc;background:#f3f3f3;padding:1px 6px;border-radius:2px}
.underline{height:1px;background:#bbb;width:84px}
.post{display:flex;gap:16px;width:320px}
.avatar{width:46px;height:46px;border-radius:50%;background:radial-gradient(circle,#d9d4cc,#9c958b);flex:none;border:2px solid #eee}
.post p{font-size:9px;color:#222;line-height:1.35}
.post .date{color:var(--red);font-size:9px;margin-top:4px}
.tweet{display:flex;gap:18px;width:270px}
.tweet .avatar{width:36px;height:36px}
.tweet b{font-weight:400;font-size:8.5px;color:#222}
.tweet p{font-size:7px;color:var(--muted);line-height:1.1}
.tweet .date{color:var(--red);font-size:8.5px}
.pager{left:465px;top:1107px;display:flex;gap:5px}
.pager span{width:15px;height:15px;border-radius:50%;border:1px solid #444;display:flex;align-items:center;justify-content:center}
.footer{left:0;top:1138px;width:1042px;height:62px;background:var(--footer);color:#ddd}
.footer .links{position:absolute;left:198px;top:10px;font-size:8.5px}
.footer .links span+span::before{content:"|";margin:0 5px}
.footer .copy{position:absolute;left:198px;top:37px;font-size:7.5px}
.footer .partner{position:absolute;left:640px;top:16px;font-size:26px;color:#2fa4e7;font-weight:700;display:flex;align-items:center;gap:8px}
.footer .partner i{width:18px;height:18px;border-radius:50%;background:#2fa4e7;display:inline-block}
</style>
</head>
<body>
<header>
  <div class="abs topbar"></div>
  <div class="abs brand">Kellaway Show</div>
  <div class="abs phone">
    <svg width="13" height="11" viewBox="0 0 13 11"><path d="M1 3c0-2 11-2 11 0v2H9V3.5H4V5H1z M3 6h7l2 5H1z" fill="#fff"/></svg>
    123-456-789
  </div>
  <div class="abs follow">Follow us :<span class="sq"></span><span class="sq"></span><span class="sq"></span><span class="sq"></span></div>
  <nav class="abs nav"><ul><li>HOME</li><li>ABOUT</li><li>UPCOMING SHOWS</li><li>PAST SHOWS</li><li>RADIO SHOW</li><li>BLOG</li><li>CONTACT US</li></ul></nav>
</header>

<section>
  <div class="abs hero" role="img" aria-label="Sepia concert crowd with a vintage studio microphone"></div>
  <div class="abs hero-mic" role="img" aria-label="Vintage microphone"></div>
  <div class="abs hero-title">Kellaway Show</div>
  <p class="abs hero-copy">Lorem ipsum dolor sit amet, consectetur adipiscing elit. Nunc sodales, nisi sodales pharetra hendrerit, tellus mi pharetra risus, sed porttitor sLorem ipsum dolor sit amet, consectetur adipiscing elit. Nunc sodales, nisi sodales pharetra hendrerit, tellus mi pharetra risus, sed porttitor sLorem ipsum dolor sit amet, consectetur adipiscing elit. Nunc sodales, nisi sodales pharetr</p>
  <div class="abs arrow" style="left:0"><svg width="14" height="18"><path d="M11 2 4 9l7 7" stroke="#fff" stroke-width="3" fill="none"/></svg></div>
  <div class="abs arrow" style="left:1007px;width:35px"><svg width="14" height="18"><path d="M3 2l7 7-7 7" stroke="#fff" stroke-width="3" fill="none"/></svg></div>
  <div class="abs dots"><span></span><span class="on"></span><span></span><span></span></div>
</section>

<section>
  <h2 style="left:205px;top:469px">Welcome to Kellaway Show</h2>
  <div class="abs body-copy" style="left:205px;top:497px;width:510px">
    <p>Lorem ipsum dolor sit amet, consectetur adipiscing elit. Nunc sodales, nisi sodales pharetra hendrerit, tellus mi pharetra risus, sed porttitor sapien dui sit amet lacus. Duis sit amet lit nec turpis.Lorem ipsum dolor sit amet, consectetur adipiscing elit. Nunc sodales, nisi sodales pharetra hendrerit</p>
    <p style="margin-top:4px">Lorem ipsum dolor sit amet, consectetur adipiscing elit. Nunc sodales, nisi sodales pharetra hendrerit, tellus mi pharetra risus, sed porttitor sapien dui sit amet lacus. Duis sit amet lit nec turpis.Lorem ipsum dolor sit amet, consectetur adipiscing elit. Nunc sodales, nisi sodales pharetra hendrerit Lorem Lorem ipsum dolor sit amet, consectetur adipiscing elit. Nunc sodales, nisi sodales pharetra hendrerit, tellus mi pharetra risus, sed porttitor sapien dui sit amet lacus. Duis sit amet lit nec turpis.Lorem ipsum dolor sit amet, consectetur adipiscing elit. Nunc sodales, nisi sodales pharetra hendrerit Lorem</p>
  </div>
  <div class="abs" role="img" aria-label="Studio microphone with headphones" style="left:722px;top:472px;width:139px;height:120px;background:radial-gradient(circle at 50% 45%,#d8d8d8,#444 45%,#000 75%)"></div>
  <div class="abs more" style="left:788px;top:606px">Read more &gt;&gt;</div>
</section>

<section>
  <h2 style="left:205px;top:636px">Past Shows</h2>
  <div class="abs" style="left:437px;top:639px;display:flex;gap:3px">
    <svg width="13" height="12"><rect width="13" height="12" fill="#333"/><path d="M8 3 5 6l3 3" stroke="#fff" fill="none"/></svg>
    <svg width="13" height="12"><rect width="13" height="12" fill="#333"/><path d="M5 3l3 3-3 3" stroke="#fff" fill="none"/></svg>
  </div>
  <div class="abs photo" role="img" aria-label="Concert crowd under purple stage lights" style="left:206px;top:666px;width:267px;height:199px"></div>
  <div class="abs showcard">
    <div class="name">SHOW NAME</div>
    <div class="desc">Lorem ipsum dolor sit amet, consectetur adipiscing elit. Nunc sodales, nisi sodales</div>
    <div class="share">SHARE THIS VIDEO <i style="margin-left:6px"></i><i></i><i></i><i></i><i></i></div>
    <div class="date">03<br>FEB</div>
  </div>

  <h2 style="left:525px;top:638px">Upcoming Shows</h2>
  <div class="abs" style="left:525px;top:664px;color:var(--red);font-size:15px;font-weight:700">KELLAWAY SHOW</div>
  <div class="abs" style="left:526px;top:683px;font-size:8.5px">10 Feb, 2014</div>
  <div class="abs photo" role="img" aria-label="Concert crowd under purple stage lights" style="left:690px;top:664px;width:156px;height:117px"></div>
  <p class="abs body-copy" style="left:525px;top:702px;width:154px">Lorem ipsum dolor sit amet, consectetur adipiscing elit. Nunc sodales, nisi sodales pharetra hendrerit, tellus mi pharetra risus, sed porttitor sapien dui sit amet lacus. Duis sit amet lit n tellus mi pharetra risus, sed</p>
  <p class="abs body-copy" style="left:525px;top:787px;width:325px">Lorem ipsum dolor sit amet, consectetur adipiscing elit. Nunc sodales, nisi sodales pharetra hendrerit, tellus mi pharetra risus, sed porttitor sapien dui sit amet lacus. Duis sit amet lit nec turpis.Lorem ipsum dolor sit amet, consectetur adipiscing elit. Nunc sodales, nisi sodales pharetra hendrerit Lorem Lorem ipsum dolor sit amet, consectetur adipiscing elit. Nunc sodales, nisi sodales pharetra hendrerit, tellus mi pharetra risus, sed porttitor sapien dui sit amet lacus. Duis sit amet lit nec turpis.Lorem ipsum dolor sit amet, consectetur adipiscing elit. Nunc sodales, nisi sodales pharetra hendrerit Lorem</p>
  <div class="abs more" style="left:788px;top:885px">Read more &gt;&gt;</div>
  <div class="abs" style="left:526px;top:904px;font-size:7.5px">Posted by Admin on Feb 08, 2014</div>
  <div class="abs socialbar">
    <span class="btn">Share</span><span>942</span>
    <span class="btn">Share</span><span>45</span>
    <span class="btn">Share</span><span>161</span>
    <span class="btn">Share</span><span>208</span>
  </div>
</section>

<section>
  <h2 style="left:212px;top:955px">Recent Blog Post</h2>
  <div class="abs underline" style="left:212px;top:980px"></div>
  <div class="abs post" style="left:212px;top:993px">
    <div class="avatar" role="img" aria-label="Author portrait"></div>
    <div><p>Lorem ipsum dolor sit amet, consectetur adipiscing elitLorem ipsum dolor sit amet, consectetur adipiscing elit</p><div class="date">08 Feb, 2014</div></div>
  </div>
  <div class="abs post" style="left:212px;top:1060px">
    <div class="avatar" role="img" aria-label="Author portrait"></div>
    <div><p>Lorem ipsum dolor sit amet, consectetur adipiscing elitLorem ipsum dolor sit amet, consectetur adipiscing</p><div class="date">08 Feb, 2014</div></div>
  </div>
  <div class="abs pager">
    <span><svg width="6" height="7"><path d="M5 1 2 3.5 5 6" stroke="#333" fill="none"/></svg></span>
    <span><svg width="6" height="7"><path d="M1 1l3 2.5L1 6" stroke="#333" fill="none"/></svg></span>
  </div>

  <h2 style="left:556px;top:955px">Latest Tweets</h2>
  <div class="abs underline" style="left:556px;top:980px"></div>
  <div class="abs tweet" style="left:558px;top:987px"><div class="avatar" role="img" aria-label="Follower portrait"></div><div><b>Demo@name</b><p>Lorem ipsum dolor sit amet, consectetur adipiscing elitL orem ipsum dolor sit amet, consectetur adipiscing elit</p><div class="date">Posted on 08th Feb</div></div></div>
  <div class="abs tweet" style="left:558px;top:1036px"><div class="avatar" role="img" aria-label="Follower portrait"></div><div><b>Demo@name</b><p>Lorem ipsum dolor sit amet, consectetur adipiscing elitL orem ipsum dolor sit amet, consectetur adipiscing elit</p><div class="date">Posted on 08th Feb</div></div></div>
  <div class="abs tweet" style="left:558px;top:1083px"><div class="avatar" role="img" aria-label="Follower portrait"></div><div><b>Demo@name</b><p>Lorem ipsum dolor sit amet, consectetur adipiscing elitL orem ipsum dolor sit amet, consectetur adipiscing elit</p><div class="date">Posted on 08th Feb</div></div></div>
</section>

<footer class="abs footer">
  <div class="links"><span>Contact</span><span>Supporters</span><span>Newsletter</span><span>Policies</span><span>Available from TuneStore</span></div>
  <div class="copy">© 2014, All Rights Reserved</div>
  <div class="partner"><i></i>OrbitalWave</div>
</footer>
</body>
</html>
```